International Clinical Software Company needs a new business card design

We are looking for a new business card design for our company that has recently expanded into the UK market, making us a multinational company.
After having rebranded our website and produced a new style guide, we are looking for a business card that is creative and attention grabbing, while being consistent with the style and colour scheme used on the new website, www.plumvora.example
We produce care management technology for the aged care market, but the main aspect we aim to communicate is the human element of our software, and the way it assists in providing better care for aged people, and stronger relationships between aged people and the staff that care for them.
Our current business card is a dark green with gold text, which makes the text quite difficult to read, not very aesthetically appealing and the colour scheme looks quite dated.
We would like something fresh and modern, that can still be colourful but doesn't use large blocks of dark colour, and uses the colours within our logo.
Something tying in with the leaves that are used in our logo could work quite nicely, along with the Autumn/Fall colours of soft greens, yellows and reds (also in our existing logo). However also happy to look at fresh, completely out of the box ideas we may not have yet considered.
Target Market(s)
The people that receive this business card work in the aged card or health industry and are either corporate/management level staff or clinical (Registered Nurses, care workers etc.)
Industry/Entity Type
Health Product
Contact Information for Business Card
Company Name - BrindlewayCare
Company locations: United Kingdom, Australia, New Zealand
Staff Details:
Staff name: Derek Mallow
Staff job title: Executive Chairman
Staff email: d.mallow@plumvora.example
Office phone number: 01742 918576
Font styles to use
Other font styles liked:
- Calibri
Requirements
Must have
- Must include the BrindlewayCare brand name in it's current font
- Must include logo (3 leaves in gold circle)
- Must include Business Card Details
Nice to have
- Elements of gold
- White space
- Something autumn themed but not too cliched
Should not have
- No blue - used by a major competitor and we would like to differentiate from them
- Large blocks of dark green colour (the green that appears in our leaves on the logo on our current business card is the background colour and it is far too dark)

```html
<!DOCTYPE html>
<html lang="en">
<head>
<meta charset="utf-8">
<title>BrindlewayCare – Business Card</title>
<link rel="stylesheet" href="https://fonts.googleapis.com/css2?family=Open+Sans:wght@300;400;600&display=swap">
<style>
  :root {
    --page-bg: #d8d3cb;
    --card-bg: #f1efeb;
    --card-edge: #ffffff;
    --gold: #8a7350;
    --wine: #8c1d3a;
    --ink: #5a4f46;
  }
  * { box-sizing: border-box; margin: 0; padding: 0; }
  html, body {
    width: 1200px;
    height: 969px;
    overflow: hidden;
    background: var(--page-bg);
    font-family: "Open Sans", Calibri, sans-serif;
  }
  .canvas {
    position: relative;
    width: 1200px;
    height: 969px;
    display: flex;
    align-items: center;
    justify-content: center;
  }
  .business-card {
    position: relative;
    width: 1000px;
    height: 570px;
    background: var(--card-bg);
    border: 2px solid var(--card-edge);
    border-radius: 34px;
    overflow: hidden;
    box-shadow: 0 18px 40px rgba(60, 50, 40, 0.18);
  }
  .details {
    position: absolute;
    left: 70px;
    top: 78px;
    width: 400px;
  }
  .brand-name {
    font-weight: 300;
    font-size: 46px;
    line-height: 1;
    color: var(--gold);
    white-space: nowrap;
  }
  .person-name {
    margin-top: 40px;
    font-weight: 600;
    font-size: 30px;
    line-height: 1.15;
    color: var(--gold);
  }
  .person-title {
    font-weight: 400;
    font-size: 25px;
    line-height: 1.3;
    color: var(--wine);
  }
  .locations {
    list-style: none;
    margin-top: 22px;
  }
  .locations li {
    position: relative;
    padding-left: 26px;
    font-size: 23px;
    line-height: 37px;
    color: var(--ink);
  }
  .locations li::before {
    content: "";
    position: absolute;
    left: 4px;
    top: 15px;
    width: 8px;
    height: 8px;
    border-radius: 50%;
    background: var(--gold);
  }
  .contacts {
    list-style: none;
    margin-top: 20px;
  }
  .contacts li {
    display: flex;
    align-items: center;
    gap: 14px;
    font-size: 21px;
    line-height: 37px;
    color: var(--ink);
    white-space: nowrap;
  }
  .contacts svg {
    width: 21px;
    height: 21px;
    flex: none;
    fill: var(--gold);
  }
  .brand-mark {
    position: absolute;
    left: 414px;
    top: 0;
    width: 586px;
    height: 570px;
  }
  .brand-mark-label {
    position: absolute;
    inset: 0;
    display: flex;
    align-items: center;
    justify-content: center;
    font-weight: 300;
    font-size: 42px;
    color: var(--gold);
  }
</style>
</head>
<body>
<main class="canvas">
  <article class="business-card">
    <section class="details">
      <h1 class="brand-name">BrindlewayCare</h1>
      <h2 class="person-name">Derek Mallow</h2>
      <p class="person-title">Executive Chairman</p>
      <ul class="locations">
        <li>United Kingdom</li>
        <li>Australia</li>
        <li>New Zealand</li>
      </ul>
      <ul class="contacts">
        <li>
          <svg viewBox="0 0 24 24" aria-hidden="true"><path d="M6.6 10.8a15.1 15.1 0 0 0 6.6 6.6l2.2-2.2c.3-.3.7-.4 1-.2 1.1.4 2.3.6 3.6.6.6 0 1 .4 1 1V20c0 .6-.4 1-1 1A17 17 0 0 1 3 4c0-.6.4-1 1-1h3.5c.6 0 1 .4 1 1 0 1.3.2 2.5.6 3.6.1.3 0 .7-.2 1z"/></svg>
          <span>01742 918576</span>
        </li>
        <li>
          <svg viewBox="0 0 24 24" aria-hidden="true"><path d="M2 5h20v2l-10 7L2 7z"/><path d="M2 9l10 7 10-7v10H2z"/></svg>
          <span>d.mallow@plumvora.example</span>
        </li>
        <li>
          <svg viewBox="0 0 24 24" aria-hidden="true"><circle cx="12" cy="12" r="10"/><path d="M12 2c-3 3-3 17 0 20M12 2c3 3 3 17 0 20M2.5 9h19M2.5 15h19" fill="none" stroke="#f1efeb" stroke-width="1.4"/></svg>
          <span>www.plumvora.example</span>
        </li>
      </ul>
    </section>

    <div class="brand-mark">
      <svg width="586" height="570" viewBox="0 0 586 570" aria-hidden="true">
        <circle cx="284" cy="285" r="262" fill="none" stroke="var(--gold)" stroke-width="8"/>
      </svg>
      <div class="brand-mark-label">BrindlewayCare</div>
    </div>
  </article>
</main>
</body>
</html>
```